Website for "Nodo de Soluciones Verdantes"

We need a new web design for an enterprise dedicated to environment and energy saving engineering, based in Monterrey, Mexico.
They offer consulting services, mainly to enhance building designs, and they are also resellers for several products in the energy saving field.

The final design should be oriented to engineers and architects, and should communicate professionalism, innovation, environment care.

Here is the website of a partner enterprise, which does pretty much the same:

http://www.cirelumen.com/

Target Market(s)

mainly architects and engineers looking for solutions on energy efficiency building

Industry/Entity Type

Environment

Requirements
Must have
• Entry page must be quite graphical and intuitive, must have a "products listing" and a "projects portfolio".

```html
<!DOCTYPE html>
<html lang="en">
<head>
<meta charset="utf-8">
<title>Nodo de Soluciones Verdantes — Energy &amp; Building Intelligence</title>
<link rel="stylesheet" href="https://fonts.googleapis.com/css2?family=Source+Sans+3:ital,wght@0,400;0,600;0,700;1,400;1,600&display=swap">
<style>
:root{
  --orange:#f06a28;
  --orange-dark:#e2561a;
  --red:#e0262b;
  --teal:#18a2a6;
  --navy:#4b4891;
  --navy-dark:#3a3778;
  --green:#6bbd3a;
  --green-light:#8ccf4c;
  --text:#666;
  --text-dark:#333;
  --grey-band:#f2f2f2;
  --frame:#dcdcdc;
}
*{box-sizing:border-box;margin:0;padding:0}
html,body{width:895px;height:1200px;overflow:hidden}
body{position:relative;background:#fff;font-family:"Source Sans 3",sans-serif;color:var(--text)}
.abs{position:absolute}

.top-bar{left:0;top:0;width:895px;height:5px;background:var(--orange)}

/* header */
.brand{left:92px;top:38px;display:flex;align-items:center;gap:8px}
.brand-mark{width:26px;height:26px;border-radius:50%;background:var(--green)}
.brand-name{font-size:17px;font-weight:600;color:var(--navy);line-height:1}
.brand-tag{left:126px;top:64px;font-size:9.5px;color:#777}
.social{left:724px;top:16px;display:flex;gap:8px}
.social span{width:18px;height:18px;border-radius:3px}
.social .s1{background:#6cb6d6}.social .s2{background:#4c67a8}.social .s3{background:#f39a2a}
.search{left:507px;top:55px;width:163px;height:26px;border:1px solid #ddd;border-radius:4px;box-shadow:0 3px 5px rgba(0,0,0,.08);font-size:8px;color:#666;padding:8px 12px}
.search svg{position:absolute;right:9px;top:6px}
.contact-label{right:98px;top:48px;font-size:12px;color:var(--green)}
.contact-phone{right:98px;top:59px;font-size:18.5px;color:var(--teal)}

/* nav */
.main-nav{left:89px;top:113px;width:717px;height:36px;background:linear-gradient(#5a57a0,var(--navy));box-shadow:0 3px 6px rgba(0,0,0,.2);z-index:3}
.main-nav a{color:#fff;text-decoration:none;font-size:13px;font-weight:600;position:absolute;top:10px}
.main-nav .home{left:0;top:0;width:102px;height:36px;background:linear-gradient(var(--green-light),var(--green));text-align:center;line-height:36px}

/* hero */
.hero{left:0;top:131px;width:895px;height:322px;background:linear-gradient(180deg,#3da7e6 0%,#9fd8f6 45%,#cfeefc 76%,#7fc23a 80%,#5ea92a 100%)}
.hero-title{left:107px;top:244px;font-size:24px;color:#1d2b3a}
.hero-text{left:108px;top:276px;font-size:11px;line-height:17px;color:#1d2b3a;width:290px}
.hero-arrow{top:322px;width:24px;height:24px;border-radius:50%;background:#6a6f75}
.hero-arrow svg{display:block;margin:7px auto}
.hero-shadow{left:60px;top:453px;width:775px;height:10px;background:radial-gradient(ellipse at top,rgba(0,0,0,.18),transparent 70%)}

/* welcome */
.welcome{left:0;top:463px;width:895px;text-align:center}
.welcome h1{font-weight:400;font-size:20px;color:var(--orange);margin-top:2px}
.welcome h2{font-weight:400;font-size:13px;color:var(--red);margin-top:3px}
.welcome p{width:660px;margin:7px auto 0;font-size:10.3px;line-height:17px;color:#666}
.btn{display:inline-block;background:linear-gradient(#5a57a0,var(--navy-dark));color:#fff;border-radius:5px;text-decoration:none}
.btn-more{margin-top:4px;font-size:11.5px;padding:4px 9px;border:1px solid #2f2c66}
.btn-small{position:absolute;font-size:11px;font-style:italic;width:62px;height:19px;text-align:center;line-height:19px;border-radius:6px}

/* products */
.products{left:0;top:612px;width:895px;height:246px;background:var(--grey-band)}
.section-title{position:absolute;font-weight:400;color:var(--orange)}
.products .section-title{left:79px;top:10px;font-size:19px}
.product{position:absolute;top:44px;width:212px;height:190px}
.thumb{border:2px solid #fff;outline:1px solid var(--frame)}
.product .thumb{height:97px}
.product h3{font-weight:400;font-size:11.5px;color:#555;margin-top:7px}
.product p{font-size:9.3px;line-height:15px;color:#888;margin-top:2px;width:212px}
.product .btn-small{left:150px;top:165px}

/* lower */
.lower .section-title{font-size:16px}
.news-item{position:absolute;left:86px;width:220px}
.news-item .thumb{position:absolute;left:0;top:0;width:79px;height:71px}
.news-item h4{position:absolute;left:86px;top:0;font-weight:400;font-size:13px;color:var(--teal)}
.news-item p{position:absolute;left:87px;top:22px;font-size:10px;line-height:12.5px;color:#666;width:130px}
.arrows{display:flex;gap:2px}
.client{left:338px;top:911px;font-size:12px;font-weight:600;color:#999}
.quote{left:340px;top:929px;width:132px;font-size:9.2px;line-height:13.6px;color:#555;text-align:justify}
.quote .mark{color:#c7e0a0;font-size:16px;font-style:italic;line-height:0}
.client-photo{left:479px;top:926px;width:72px;height:66px}
.url{left:340px;top:1025px;font-size:7.5px;color:#333}
.share{top:1045px;height:14px;border:1px solid #ccc;border-radius:2px;font-size:7.5px;color:#333;padding:0 4px;display:flex;align-items:center;gap:3px;background:#f7f7f7}
.share i{width:9px;height:9px;display:inline-block;border-radius:2px}
.count{top:1045px;height:14px;border:1px solid #ccc;font-size:7.5px;padding:0 4px;line-height:12px;color:#333}

/* footer */
.footer{left:0;top:1128px;width:895px;height:72px;background:linear-gradient(var(--orange),var(--orange-dark));border-top:2px solid #f7a06a}
.footer-nav a{position:absolute;top:15px;color:#fff;text-decoration:none;font-size:11px}
.footer .copy{position:absolute;top:40px;left:0;width:895px;text-align:center;font-size:11px;color:#fff}
</style>
</head>
<body>
<div class="abs top-bar"></div>

<header>
  <div class="abs brand"><span class="brand-mark"></span><span class="brand-name">Nodo de Soluciones Verdantes</span></div>
  <div class="abs brand-tag">Energy &amp; Building Intelligence</div>
  <div class="abs social" aria-label="Social links"><span class="s1"></span><span class="s2"></span><span class="s3"></span></div>
  <div class="abs search">Search
    <svg width="13" height="13" viewBox="0 0 13 13"><circle cx="5.5" cy="5.5" r="4.2" fill="none" stroke="#888" stroke-width="1.3"/><line x1="8.5" y1="8.5" x2="12" y2="12" stroke="#666" stroke-width="2"/></svg>
  </div>
  <div class="abs contact-label">Contact Us</div>
  <div class="abs contact-phone">1800 555 0147</div>
</header>

<nav class="abs main-nav">
  <a class="home" href="#">Home</a>
  <a href="#" style="left:114px">The Company</a>
  <a href="#" style="left:229px">Products</a>
  <a href="#" style="left:316px">Project&nbsp; Portfolio</a>
  <a href="#" style="left:447px">Photo Gallery</a>
  <a href="#" style="left:561px">News</a>
  <a href="#" style="left:629px">Contacts</a>
</nav>

<section class="abs hero" role="img" aria-label="Bright blue sky over a green meadow with a lone tree and a small farmhouse"></section>
<div class="abs hero-title">Duis tincidunt lectus quis</div>
<div class="abs hero-text">Vivamus porttitor purus nisi eleifend libero, a tempus libero lectus feugiat felis Morbi diam mauris viverra.</div>
<div class="abs hero-arrow" style="left:111px"><svg width="8" height="10"><path d="M6 1 2 5l4 4" fill="none" stroke="#fff" stroke-width="2"/></svg></div>
<div class="abs hero-arrow" style="left:138px"><svg width="8" height="10"><path d="M2 1l4 4-4 4" fill="none" stroke="#fff" stroke-width="2"/></svg></div>
<div class="abs hero-shadow"></div>

<section class="abs welcome">
  <h1>WELCOME TO NODO DE SOLUCIONES VERDANTES</h1>
  <h2>Energy &amp; Building Inteligence</h2>
  <p>But I must explain to you how all this mistaken idea of denouncing pleasure and praising pain was born and I will give you a complete account of the system, and expound the actual teachings of the great explorer of the truth, the master-builder of human happiness. No one rejects, dislikes, or avoids pleasure itself, because it is pleasure, but because those who do not know how to pursue</p>
  <a class="btn btn-more" href="#">Know more</a>
</section>

<section class="abs products">
  <h2 class="section-title">Products Listing</h2>
  <div class="product" style="left:79px">
    <div class="thumb" role="img" aria-label="Construction worker laying bricks against an orange sky" style="background:linear-gradient(90deg,#4a6a3a,#c98a4a 60%,#e0a070)"></div>
    <h3>Phasellus felis</h3>
    <p>Morbi eget arcu. Morbi porta, libero id ullamcorper nonummy, nibh ligula pulvinar metus, eget con-sectetuer</p>
    <a class="btn btn-small" href="#">Click here</a>
  </div>
  <div class="product" style="left:341px">
    <div class="thumb" role="img" aria-label="Technician installing solar panels on a roof" style="background:linear-gradient(180deg,#6aa8e0,#3a5fb0 55%,#22387a)"></div>
    <h3>Phasellus felis</h3>
    <p>Morbi eget arcu. Morbi porta, libero id ullamcorper nonummy, nibh ligula pulvinar metus, eget con-sectetuer</p>
    <a class="btn btn-small" href="#">Click here</a>
  </div>
  <div class="product" style="left:603px">
    <div class="thumb" role="img" aria-label="Engineers in hard hats at a building site" style="background:linear-gradient(90deg,#2a3f6a,#6a88b0 50%,#b06a30)"></div>
    <h3>Phasellus felis</h3>
    <p>Morbi eget arcu. Morbi porta, libero id ullamcorper nonummy, nibh ligula pulvinar metus, eget con-sectetuer</p>
    <a class="btn btn-small" href="#">Click here</a>
  </div>
</section>

<section class="lower">
  <h2 class="section-title" style="left:85px;top:878px">RECENT NEWS</h2>
  <div class="news-item" style="top:917px">
    <div class="thumb" role="img" aria-label="Solar panels under a blue sky" style="background:linear-gradient(180deg,#7ab6ea,#2e4f9a)"></div>
    <h4>Lorium ipsum</h4>
    <p>Lorem ipsum dolor sit amet, consectetur adipiscing elit. Phasellus a magna dolor.</p>
  </div>
  <div class="news-item" style="top:998px">
    <div class="thumb" role="img" aria-label="Worker mounting a solar panel array" style="background:linear-gradient(180deg,#8ab8e8,#3050a0)"></div>
    <h4>Lorium ipsum</h4>
    <p>Lorem ipsum dolor sit amet, consectetur adipiscing elit. Phasellus a magna dolor.</p>
  </div>
  <a class="btn btn-small" href="#" style="left:232px;top:1073px">Click here</a>

  <h2 class="section-title" style="left:338px;top:875px">TESTIMONIALS</h2>
  <div class="abs arrows" style="left:524px;top:881px" aria-label="Previous and next">
    <svg width="9" height="12" viewBox="0 0 9 12"><path d="M7 1.5 2.5 6 7 10.5" fill="none" stroke="#f06a28" stroke-width="2.6"/></svg>
    <svg width="9" height="12" viewBox="0 0 9 12"><path d="M2 1.5 6.5 6 2 10.5" fill="none" stroke="#f06a28" stroke-width="2.6"/></svg>
  </div>
  <div class="abs client">CLIENT NAME</div>
  <p class="abs quote"><span class="mark">“</span> Sed ut perspiciatis unde omnis iste natus error sit voluptatem accusantium doloremque laudantium, totam rem aperiam, quasi architecto beatae vitae dicta sunt explicabo. hgioo9 <span class="mark">”</span></p>
  <div class="abs thumb client-photo" role="img" aria-label="Portrait of the client" style="background:linear-gradient(180deg,#8a8f94,#5e6268)"></div>
  <div class="abs url">HTTP://SOCIAL.NODOVERDANTES.COM/CLIENT</div>
  <div class="abs share" style="left:340px"><i style="background:#6cb6d6"></i>Post</div>
  <div class="abs count" style="left:384px">0</div>
  <div class="abs share" style="left:400px"><i style="background:#2a6fa8"></i>Share</div>
  <div class="abs share" style="left:448px"><i style="background:#d9453a"></i>Send</div>
  <div class="abs count" style="left:494px">0</div>
  <a class="btn btn-small" href="#" style="left:494px;top:1073px">Click here</a>

  <h2 class="section-title" style="left:583px;top:875px">PROJECTS PORTFOLIO</h2>
  <div class="abs arrows" style="left:774px;top:881px" aria-label="Previous and next">
    <svg width="9" height="12" viewBox="0 0 9 12"><path d="M7 1.5 2.5 6 7 10.5" fill="none" stroke="#f06a28" stroke-width="2.6"/></svg>
    <svg width="9" height="12" viewBox="0 0 9 12"><path d="M2 1.5 6.5 6 2 10.5" fill="none" stroke="#f06a28" stroke-width="2.6"/></svg>
  </div>
  <div class="abs thumb" role="img" aria-label="Two engineers in hard hats reviewing plans" style="left:582px;top:905px;width:222px;height:86px;background:linear-gradient(90deg,#3a5a8a,#b8c8dc 50%,#6a86aa)"></div>
  <div class="abs thumb" role="img" aria-label="Crane and hard hat on site" style="left:582px;top:995px;width:70px;height:67px;background:linear-gradient(135deg,#2a2a2a,#8a7a50)"></div>
  <div class="abs thumb" role="img" aria-label="Worker on a solar panel" style="left:658px;top:995px;width:70px;height:67px;background:linear-gradient(180deg,#7ab0e6,#2a4a96)"></div>
  <div class="abs thumb" role="img" aria-label="Architectural model of buildings" style="left:735px;top:995px;width:70px;height:67px;background:linear-gradient(135deg,#f4f4f4,#9a9a9a)"></div>
  <a class="btn btn-small" href="#" style="left:748px;top:1073px">Click here</a>
</section>

<footer class="abs footer">
  <nav class="footer-nav">
    <a href="#" style="left:165px">Home</a>
    <a href="#" style="left:232px">The Company</a>
    <a href="#" style="left:334px">Products</a>
    <a href="#" style="left:412px">Project&nbsp; Portfolio</a>
    <a href="#" style="left:526px">Photo Gallery</a>
    <a href="#" style="left:626px">News</a>
    <a href="#" style="left:688px">Contacts</a>
  </nav>
  <div class="copy">Copyright &copy; 2013 &nbsp;&nbsp; www.nodoverdantes.com &nbsp;&nbsp; All rights reserved.</div>
</footer>
</body>
</html>
```